Video Editing Website - Wordpress Design Project

Hi There
I am setting up a Tribute Funeral Video and Home Video Editing Website for my Company. "Reel Harbor". This is to assist people with putting together their Videos and Photos with music to show at a Funeral or for Family Memories. I already have a domain www.reelharbor.com.au, but I have no host yet.

Some websites that already do this are http://www.quietlantern.com.au/tributes, http://www.cobaltframeworks.com.au/services/funeral-tribute-videos.html, and http://www.sundialkeepsakes.com.au/
These are examples not to cpy, but to get an idea of what I am offering so you can design accordingly.

I have a logo which is attached. You will see that the logo is mainly blue, so I would appreciate a website with that colour on the pages, but not ALL over the page.

I would like to upload videos occasionally from clipnest.com so I would appreciate that option incorporated.

Thank you lots.
Gareth

Target Market(s)

Families predominately in the 25-60 age range

Industry/Entity Type

It Company

Requirements
Must have
• *Ability to upload Videos from clipnest.com
*Ability for me to edit the content whenever I need to
*A contact page to send email messages to me

```html
<!DOCTYPE html>
<html lang="en">
<head>
<meta charset="utf-8">
<title>Reel Harbor – Home</title>
<link rel="stylesheet" href="https://fonts.googleapis.com/css2?family=Oswald:wght@400&family=Arimo:wght@400;700&display=swap">
<style>
  :root {
    --page-bg: #d3e5f5;
    --top-bar: #2b2b2b;
    --brand-blue: #1f6cb6;
    --brand-blue-dark: #185b9c;
    --orange: #f56a08;
    --orange-light: #f9852a;
    --text-grey: #555555;
    --heading-grey: #5a5a5a;
    --panel-white: #ffffff;
    --rule: #e2e2e2;
    --footer-blue: #1d6ab6;
  }
  * { box-sizing: border-box; margin: 0; padding: 0; }
  html, body { width: 1200px; height: 1060px; overflow: hidden; }
  body {
    position: relative;
    background: radial-gradient(ellipse at 20% 60%, #e3eef8 0%, var(--page-bg) 55%, #c9def1 100%);
    font-family: "Arimo", Arial, sans-serif;
    color: var(--text-grey);
  }
  .top-bar { position: absolute; top: 0; left: 0; width: 1200px; height: 8px; background: var(--top-bar); }

  .brand { position: absolute; left: 120px; top: 58px; display: flex; align-items: center; gap: 10px; }
  .brand-mark { width: 22px; height: 22px; background: var(--brand-blue); }
  .brand-name { font-family: "Arimo", Arial, sans-serif; font-size: 30px; font-weight: 400; color: var(--brand-blue); }

  .search { position: absolute; left: 838px; top: 52px; width: 242px; height: 37px;
    background: #fff; border: 1px solid #e4e4e4; border-radius: 3px; box-shadow: 0 0 0 3px rgba(255,255,255,.6); }
  .search-btn { position: absolute; right: 0; top: 0; width: 36px; height: 35px; border-left: 1px solid #e6e6e6;
    display: flex; align-items: center; justify-content: center; }

  .main-nav { position: absolute; left: 120px; top: 136px; width: 960px; height: 41px;
    background: linear-gradient(#2576c2, var(--brand-blue-dark)); border-radius: 2px;
    display: flex; justify-content: space-between; align-items: center; padding: 0 15px; }
  .main-nav a { font-family: "Oswald", sans-serif; font-size: 15px; color: #fff; text-decoration: none; text-transform: uppercase; }

  .hero { position: absolute; left: 120px; top: 182px; width: 960px; height: 350px;
    background: linear-gradient(120deg, #e9d3c2 0%, #f3e6db 30%, #c9a68e 55%, #a7c7d8 70%, #7fa46b 100%); }
  .hero-dots { position: absolute; left: 552px; top: 513px; width: 92px; height: 16px; border-radius: 8px 8px 0 0;
    background: rgba(255,255,255,.5); display: flex; gap: 5px; justify-content: center; align-items: center; }
  .hero-dots span { width: 10px; height: 10px; border-radius: 50%; background: #9b9b9b; border: 1px solid #fff; }
  .hero-dots span.active { background: #444; }

  .service { position: absolute; top: 544px; width: 300px; height: 151px; background: var(--panel-white);
    box-shadow: 0 2px 3px rgba(0,0,0,.12); }
  .service h2 { height: 40px; background: linear-gradient(var(--orange-light), var(--orange));
    font-family: "Oswald", sans-serif; font-weight: 400; font-size: 17px; color: #fff; line-height: 40px; padding-left: 9px; }
  .service p { font-size: 11.5px; line-height: 16px; text-align: justify; padding: 8px 6px 0 5px; color: #666; }
  .service .more { position: absolute; right: -1px; bottom: -12px; width: 102px; height: 31px; border-radius: 16px;
    background: linear-gradient(#fafafa, #e3e3e3); border: 1px solid #d4d4d4;
    font-family: "Oswald", sans-serif; font-size: 13px; color: var(--orange); text-align: center; line-height: 29px; text-decoration: none; }

  .panel { position: absolute; top: 717px; width: 480px; height: 245px; background: var(--panel-white); }
  .panel h2 { font-family: "Oswald", sans-serif; font-weight: 400; font-size: 20px; color: var(--heading-grey);
    height: 48px; line-height: 50px; padding-left: 10px; border-bottom: 1px solid var(--rule); margin: 0 10px 0 0; }
  .panel h2 em { font-style: normal; color: var(--brand-blue); }
  .panel-img { position: absolute; left: 10px; top: 60px; width: 210px; height: 170px; }
  .panel-text { position: absolute; left: 230px; top: 56px; width: 240px; font-size: 11.5px; line-height: 16px; text-align: justify; color: #555; }
  .panel-text p + p { margin-top: 16px; }

  .site-footer { position: absolute; left: 0; top: 1000px; width: 1200px; height: 60px; background: var(--footer-blue); }
  .footer-links { position: absolute; left: 124px; top: 12px; font-size: 11px; color: #fff; }
  .footer-links a { color: #fff; text-decoration: none; }
  .footer-links .sep { margin: 0 5px; }
  .copyright { position: absolute; left: 124px; top: 37px; font-size: 11px; color: #fff; }
  .social { position: absolute; left: 933px; top: 23px; display: flex; gap: 17px; }
  .social a { width: 27px; height: 27px; display: block; }
  .social .s1 { background: #3b5b9d; } .social .s2 { background: #26a9e0; }
  .social .s3 { background: #c4161c; } .social .s4 { background: #d8493a; }
</style>
</head>
<body>
  <div class="top-bar"></div>

  <header>
    <div class="brand"><span class="brand-mark"></span><span class="brand-name">Reel Harbor</span></div>
    <div class="search">
      <div class="search-btn">
        <svg width="14" height="14" viewBox="0 0 14 14"><circle cx="5.5" cy="5.5" r="4" fill="none" stroke="#bbb" stroke-width="1.6"/><line x1="8.5" y1="8.5" x2="12.5" y2="12.5" stroke="#bbb" stroke-width="2"/></svg>
      </div>
    </div>
    <nav class="main-nav">
      <a href="#">Home</a><a href="#">About Us</a><a href="#">Services</a><a href="#">Packages</a>
      <a href="#">Samples</a><a href="#">Delivery</a><a href="#">FAQ</a><a href="#">Testimonials</a>
      <a href="#">Links</a><a href="#">News</a><a href="#">Contact Us</a>
    </nav>
  </header>

  <div class="hero" role="img" aria-label="Collage of family photographs of parents and children smiling and hugging"></div>
  <div class="hero-dots"><span></span><span></span><span class="active"></span><span></span><span></span><span></span></div>

  <section class="service" style="left:120px">
    <h2>PHOTOGRAPHY</h2>
    <p>Tribute Videos, also known as photo slide shows, remembrance videos and power point presentations, are one of the best ways families can remember a loved one, both at the service, as well as for many years after.</p>
    <a class="more" href="#">VIEW PACKAGES</a>
  </section>
  <section class="service" style="left:452px">
    <h2>AUDIO VISUAL HIRE</h2>
    <p>Tribute Videos, also known as photo slide shows, remembrance videos and power point presentations, are one of the best ways families can remember a loved one, both at the service, as well as for many years after.</p>
    <a class="more" href="#">VIEW PACKAGES</a>
  </section>
  <section class="service" style="left:783px">
    <h2>VIDEOGRAPHY</h2>
    <p>Tribute Videos, also known as photo slide shows, remembrance videos and power point presentations, are one of the best ways families can remember a loved one, both at the service, as well as for many years after.</p>
    <a class="more" href="#">VIEW PACKAGES</a>
  </section>

  <section class="panel" style="left:120px">
    <h2>WELCOME TO <em>REEL HARBOR!</em></h2>
    <div class="panel-img" role="img" aria-label="Photo of a smiling family of four outdoors" style="background:linear-gradient(135deg,#7fa24a,#e6c9ae 50%,#9bb0c8)"></div>
    <div class="panel-text">
      <p>Lorem ipsum dolor sit amet, consectetur adipisicing elit, sed do eiusmod tempor incididunt ut labore et dolore magna aliqua. Ut enim ad minim veniam, quis nostrud exercitation ullamco laboris nisi ut aliquip ex ea commodo consequat.</p>
      <p>Duis aute irure dolor in reprehenderit in voluptate velit esse cillum dolore eu fugiat nulla pariatur. Excepteur sint occaecat cupidatat non proident, sunt in culpa qui officia deserunt</p>
    </div>
  </section>
  <section class="panel" style="left:620px">
    <h2>PHOTOGRAPHIC SLIDESHOW DVD'S</h2>
    <div class="panel-img" role="img" aria-label="Cartoon illustration of three happy children" style="background:linear-gradient(135deg,#f6e7a8,#fbf3d6 50%,#e8b27a)"></div>
    <div class="panel-text">
      <p>Lorem ipsum dolor sit amet, consectetur adipisicing elit, sed do eiusmod tempor incididunt ut labore et dolore magna aliqua. Ut enim ad minim veniam, quis nostrud exercitation ullamco laboris nisi ut aliquip ex ea commodo consequat.</p>
      <p>Duis aute irure dolor in reprehenderit in voluptate velit esse cillum dolore eu fugiat nulla pariatur. Excepteur sint occaecat cupidatat non proident, sunt in culpa qui officia deserunt</p>
    </div>
  </section>

  <footer class="site-footer">
    <div class="footer-links">
      <a href="#">About Us</a><span class="sep">|</span><a href="#">Sitemap</a><span class="sep">|</span><a href="#">Help / FAQs</a><span class="sep">|</span><a href="#">Order Status</a><span class="sep">|</span><a href="#">Returns</a><span class="sep">|</span><a href="#">Contact Us</a>
    </div>
    <div class="copyright">Copyright © 2013 Reel Harbor | All Rights Reserved.</div>
    <div class="social">
      <a class="s1" href="#" aria-label="Social link"></a><a class="s2" href="#" aria-label="Social link"></a>
      <a class="s3" href="#" aria-label="Social link"></a><a class="s4" href="#" aria-label="Social link"></a>
    </div>
  </footer>
</body>
</html>
```